Redesign of the UI of a customer service platform

To improve the user experience of our customers, we need a new design for our agent interface of our customer service platform (tessura.com).
The focus will be on the dashboard and the inbox screens (see attached) along with the common UI elements (Buttons, menu, fonts, forms...)
We want a simple and distinctive design

Target Market(s)

Worldwide

Industry/Entity Type

It Service

Number of Pages Required

3 page

Font styles to use
Sans Serif

Requirements
Must have
• New Onboarding page: this is a new page that is shown to user the first time they login to the platform. This will replace the current onboarding screen (setup SMS, Setup widget...etc)
• Dashboard page: to access important information and activate services (see screenshot from current site)
• Inbox page: to manage all the interactions with customers. (see screenshot from current site)
• UI elements (buttons, menus, forms, tables, fonts, color palette)

```html
<!DOCTYPE html>
<html lang="en">
<head>
<meta charset="utf-8">
<title>Tessura — Agent Dashboard</title>
<link href="https://fonts.googleapis.com/css2?family=Asap:wght@400;500;600&display=swap" rel="stylesheet">
<style>
:root{
  --brand:#f35426;
  --bg:#f1f1f1;
  --white:#ffffff;
  --nav-line:#e6e6e6;
  --nav-text:#8a8a8a;
  --icon:#a5a5a5;
  --panel:#2b3346;
  --panel-ring:#262d3e;
  --panel-line:#3a4357;
  --panel-sub:#a9b0bf;
  --badge-red:#e3161e;
  --badge-yellow:#f6b800;
  --green:#3db52a;
  --text:#3d3d3d;
  --card-line:#e2e2e2;
}
*{box-sizing:border-box;margin:0;padding:0}
html,body{width:1200px;height:831px;overflow:hidden}
body{background:var(--bg);font-family:'Asap',sans-serif;position:relative;color:var(--text)}

.topbar{position:absolute;left:0;top:0;width:1200px;height:83px;background:var(--white);display:flex}
.brand{width:83px;height:83px;background:var(--brand);display:flex;align-items:center;justify-content:center;color:var(--white);font-size:14px;font-weight:500}
.nav{display:flex}
.nav-item{width:84px;height:83px;border-right:1px solid var(--nav-line);display:flex;flex-direction:column;align-items:center;padding-top:16px;position:relative;color:var(--nav-text);font-size:13px}
.nav-item svg{width:28px;height:28px;margin-bottom:7px}
.count{position:absolute;top:17px;left:45px;width:22px;height:22px;border-radius:50%;color:var(--white);font-size:12px;font-weight:600;display:flex;align-items:center;justify-content:center}
.count.red{background:var(--badge-red)}
.count.yellow{background:var(--badge-yellow)}
.avatar{position:absolute;left:1133px;top:14px;width:53px;height:53px;border-radius:50%;background:linear-gradient(160deg,#c9b3a3,#8c7466)}
.status{position:absolute;left:1128px;top:15px;width:14px;height:14px;border-radius:50%;background:var(--green)}

.hero{position:absolute;left:18px;top:102px;width:894px;height:499px;background:linear-gradient(135deg,#4a3a30 0%,#7b6a5c 35%,#9a8f86 55%,#5b4b40 80%,#3e332c 100%);overflow:hidden}
.play{position:absolute;left:399px;top:179px;width:98px;height:98px;border-radius:50%;border:6px solid var(--white);background:rgba(230,230,230,.85);display:flex;align-items:center;justify-content:center}
.hero-label{position:absolute;left:0;width:100%;top:296px;text-align:center;color:var(--white);font-size:20px}
.controls{position:absolute;left:28px;top:460px;display:flex;align-items:center;color:var(--white);font-size:12px}
.controls svg{margin-right:8px}
.track{position:absolute;left:77px;top:464px;width:790px;height:3px;background:#e8e8e8}
.track span{display:block;width:399px;height:3px;background:var(--brand)}

.plan{position:absolute;left:912px;top:102px;width:270px;height:499px;background:var(--panel);color:var(--white)}
.plan-head{position:absolute;left:18px;top:16px}
.plan-title{font-size:20px;display:flex;align-items:center}
.tag{background:var(--brand);font-size:10px;font-weight:600;padding:3px 5px;margin-left:8px;border-radius:2px}
.plan-sub{font-size:13px;color:var(--panel-sub);margin-top:3px}
.quota{position:absolute;left:0;width:270px;border-bottom:1px solid var(--panel-line)}
.quota.last{border-bottom:none}
.ring{position:absolute;left:19px;width:62px;height:62px;border-radius:50%;background:var(--panel-ring);border:1px solid var(--panel-line);display:flex;align-items:center;justify-content:center}
.name{position:absolute;left:97px;font-size:16px}
.limit{position:absolute;left:98px;font-size:12px;color:var(--panel-sub)}
.use{position:absolute;right:19px;background:var(--brand);font-size:11px;padding:2px 9px;border-radius:2px}
.buy{position:absolute;left:90px;top:447px;width:89px;height:33px;background:var(--green);color:var(--white);font-size:13px;font-weight:500;display:flex;align-items:center;justify-content:center}

.addons-title{position:absolute;left:18px;top:626px;font-size:20px;font-weight:400;color:var(--text)}
.addons{position:absolute;left:18px;top:672px;display:flex;gap:14px}
.addon{width:222px;height:83px;background:var(--white);border:1px solid var(--card-line);display:flex;position:relative}
.addon-icon{width:75px;border-right:1px solid var(--card-line);display:flex;align-items:center;justify-content:center}
.addon-body{padding:20px 0 0 17px}
.addon-name{font-size:17px;color:var(--text)}
.addon-link{font-size:11px;color:var(--brand);margin-top:5px;letter-spacing:.2px}
.active{position:absolute;right:7px;top:5px}
</style>
</head>
<body>

<header class="topbar">
  <div class="brand">tessura</div>
  <nav class="nav">
    <div class="nav-item"><svg viewBox="0 0 28 28"><path d="M3 15h7l2 3h4l2-3h7v8H3z" fill="var(--icon)"/><path d="M14 4v9M10 9l4 4 4-4" stroke="var(--icon)" stroke-width="2" fill="none"/></svg>Inbox<span class="count red">4</span></div>
    <div class="nav-item"><svg viewBox="0 0 28 28"><rect x="5" y="3" width="16" height="21" rx="1" fill="none" stroke="var(--icon)" stroke-width="2"/><path d="M9 9h8M9 13h8M9 17h5" stroke="var(--icon)" stroke-width="2"/></svg>Tasks<span class="count yellow">1</span></div>
    <div class="nav-item"><svg viewBox="0 0 28 28"><circle cx="14" cy="9" r="5" fill="var(--icon)"/><path d="M4 25c0-6 4-9 10-9s10 3 10 9z" fill="var(--icon)"/></svg>Customers</div>
    <div class="nav-item"><svg viewBox="0 0 28 28"><path d="M3 6l22 8-22 8 4-8z" fill="none" stroke="var(--icon)" stroke-width="2" stroke-linejoin="round"/><path d="M7 14h18" stroke="var(--icon)" stroke-width="2"/></svg>Campaigns</div>
    <div class="nav-item"><svg viewBox="0 0 28 28"><text x="14" y="22" text-anchor="middle" font-family="Asap,sans-serif" font-size="22" fill="var(--icon)">$</text></svg>Payments</div>
    <div class="nav-item"><svg viewBox="0 0 28 28"><path d="M5 6v18M11 3v21M17 9v15M23 6v18" stroke="var(--icon)" stroke-width="2.5"/></svg>Reports</div>
    <div class="nav-item"><svg viewBox="0 0 28 28"><circle cx="14" cy="14" r="8" fill="none" stroke="var(--icon)" stroke-width="5" stroke-dasharray="4 2.3"/><circle cx="14" cy="14" r="5" fill="var(--icon)"/><circle cx="14" cy="14" r="2.5" fill="#fff"/></svg>Settings</div>
  </nav>
  <div class="avatar" role="img" aria-label="Agent profile photo"></div>
  <span class="status"></span>
</header>

<section class="hero" role="img" aria-label="Onboarding video still: team working over papers and a tablet on a desk">
  <div class="play"><svg width="26" height="30" viewBox="0 0 26 30"><path d="M2 1l23 14-23 14z" fill="var(--brand)"/></svg></div>
  <div class="hero-label">Get Started</div>
  <div class="controls"><svg width="9" height="10" viewBox="0 0 9 10"><path d="M0 0l9 5-9 5z" fill="#fff"/></svg>0:00</div>
  <div class="track"><span></span></div>
</section>

<aside class="plan">
  <div class="plan-head">
    <div class="plan-title">Plan <span class="tag">FREE</span></div>
    <div class="plan-sub">Your trial period ends in 14 days</div>
  </div>

  <div class="quota" style="top:80px;height:107px">
    <div class="ring" style="top:25px"><svg width="34" height="30" viewBox="0 0 34 30"><circle cx="17" cy="9" r="5" fill="#fff"/><circle cx="8" cy="11" r="3.5" fill="#fff"/><circle cx="26" cy="11" r="3.5" fill="#fff"/><path d="M9 26c0-6 3-10 8-10s8 4 8 10z" fill="#fff"/><path d="M1 24c0-5 3-8 7-8 1 0 2 0 3 1-2 2-3 4-3 7zM33 24c0-5-3-8-7-8-1 0-2 0-3 1 2 2 3 4 3 7z" fill="#fff"/></svg></div>
    <div class="name" style="top:40px">Agents</div>
    <div class="limit" style="top:62px">Up to 3</div>
    <div class="use" style="top:9px">1/3</div>
  </div>

  <div class="quota" style="top:187px;height:133px">
    <div class="ring" style="top:38px"><svg width="32" height="28" viewBox="0 0 32 28"><path d="M11 6V3h10v3" stroke="#fff" stroke-width="2.5" fill="none"/><rect x="1" y="6" width="30" height="20" rx="2" fill="#fff"/><path d="M1 15h30" stroke="var(--panel-ring)" stroke-width="1.5"/><rect x="13" y="13" width="6" height="4" fill="var(--panel-ring)"/></svg></div>
    <div class="name" style="top:55px">Departments</div>
    <div class="limit" style="top:77px">Up to 3</div>
    <div class="use" style="top:25px">1/3</div>
  </div>

  <div class="quota last" style="top:320px;height:120px">
    <div class="ring" style="top:33px"><svg width="28" height="28" viewBox="0 0 28 28"><path d="M6 2l5 5-3 4c2 4 5 7 9 9l4-3 5 5-4 4C12 25 3 16 2 6z" fill="#fff"/></svg></div>
    <div class="name" style="top:46px">Phones</div>
    <div class="limit" style="top:68px">Up to 1</div>
    <div class="use" style="top:15px">1/3</div>
  </div>

  <div class="buy">BUY NOW</div>
</aside>

<h2 class="addons-title">Select Your Add-ons</h2>
<section class="addons">
  <div class="addon">
    <div class="addon-icon"><svg width="28" height="24" viewBox="0 0 28 24"><rect x="1" y="1" width="26" height="17" rx="1" fill="var(--icon)"/><rect x="3" y="3" width="22" height="12" fill="#d8d8d8"/><path d="M10 23h8M14 18v5" stroke="var(--icon)" stroke-width="2"/></svg></div>
    <div class="addon-body"><div class="addon-name">Campaigns</div><div class="addon-link">WATCH VIDEO</div></div>
  </div>
  <div class="addon">
    <div class="addon-icon"><svg width="22" height="22" viewBox="0 0 22 22"><circle cx="11" cy="11" r="10" fill="var(--icon)"/></svg></div>
    <div class="addon-body"><div class="addon-name">Messanger</div><div class="addon-link">WATCH VIDEO</div></div>
  </div>
  <div class="addon">
    <div class="addon-icon"><svg width="28" height="26" viewBox="0 0 28 26"><path d="M14 2C7 2 2 6.5 2 12c0 3 1.5 5.5 4 7.5L5 25l6-3c1 .2 2 .3 3 .3 7 0 12-4.5 12-10S21 2 14 2z" fill="var(--icon)"/><path d="M9 10h10M9 14h8" stroke="#fff" stroke-width="1.5"/></svg></div>
    <div class="addon-body"><div class="addon-name">SMS</div><div class="addon-link">WATCH VIDEO</div></div>
    <svg class="active" width="22" height="22" viewBox="0 0 22 22"><circle cx="11" cy="11" r="10" fill="var(--green)"/><path d="M6 11l3.5 3.5L16 8" stroke="#fff" stroke-width="2.4" fill="none"/></svg>
  </div>
  <div class="addon">
    <div class="addon-icon"><svg width="22" height="22" viewBox="0 0 22 22"><circle cx="11" cy="11" r="10" fill="var(--icon)"/></svg></div>
    <div class="addon-body"><div class="addon-name">Courier</div><div class="addon-link">WATCH VIDEO</div></div>
  </div>
  <div class="addon">
    <div class="addon-icon"><svg width="20" height="28" viewBox="0 0 20 28"><text x="10" y="24" text-anchor="middle" font-family="Asap,sans-serif" font-size="28" fill="var(--icon)">$</text></svg></div>
    <div class="addon-body"><div class="addon-name">Payment</div><div class="addon-link">WATCH VIDEO</div></div>
  </div>
</section>

</body>
</html>
```